Single-sided business card for restaurant velmora with new logo made on this site

Business card options with new logo including restaurant name, address, phone number and website. This business card is single-sided only and will be presented at the hostess desk for clients to take. I would like to see options based on a cream card background, a white card background, a yellow card background and a burgundy colored background. It needs to be elegant and traditional.

Target Market(s)

local and international crowd

Industry/Entity Type

restaurant

Contact Information for Business Card

address, website and phone number

Font styles to use
Serif

Colors
EE7325
F08F49
F5BC92
FAE3D3
FDF4ED

Requirements
Must have
• new logo, address, phone number, website
Should not have
• more than three colors

```html
<!DOCTYPE html>
<html lang="es">
<head>
<meta charset="utf-8">
<title>Velmora — Tarjeta de presentación</title>
<link href="https://fonts.googleapis.com/css2?family=Crimson+Text:wght@400;600&display=swap" rel="stylesheet">
<style>
  :root {
    --page: #e9e7e4;
    --card: #ffffff;
    --burgundy: #3d1b1b;
    --gold: #e8a92b;
    --ink: #3a1d1d;
  }
  * { margin: 0; padding: 0; box-sizing: border-box; }
  html, body {
    width: 1200px; height: 900px; overflow: hidden;
    background: var(--page);
    font-family: "Crimson Text", Georgia, serif;
  }
  .card {
    position: absolute; left: 100px; top: 164px;
    width: 1000px; height: 572px;
    background: var(--card);
    box-shadow: 0 10px 30px rgba(0,0,0,.18);
    overflow: hidden;
  }
  .brand {
    position: absolute; left: 96px; top: 56px;
    display: flex; flex-direction: column; align-items: flex-start;
  }
  .brand-square {
    width: 120px; height: 120px; background: var(--gold);
  }
  .brand-name {
    margin-top: 16px;
    font-size: 50px; font-weight: 600; letter-spacing: 9px;
    color: var(--ink); line-height: 1;
  }
  .contact {
    position: absolute; left: 100px; top: 288px;
    list-style: none; color: var(--ink);
    font-size: 26px; line-height: 1;
  }
  .contact li { display: flex; align-items: center; gap: 14px; margin-bottom: 14px; }
  .contact svg { width: 21px; height: 21px; flex: none; fill: var(--ink); }
  .rule {
    position: absolute; left: 0; right: 0; top: 424px;
    height: 2px; background: var(--gold);
  }
  .band {
    position: absolute; left: 0; right: 0; bottom: 0;
    height: 128px; background: var(--burgundy);
  }
  .agave-art {
    position: absolute; left: 736px; top: 250px;
    width: 200px; height: 194px;
    border-radius: 100px 100px 0 0;
    background: linear-gradient(180deg, rgba(61,27,27,0.15) 0%, rgba(61,27,27,0.75) 60%, var(--burgundy) 100%);
  }
</style>
</head>
<body>
  <main class="card">
    <div class="brand">
      <div class="brand-square"></div>
      <div class="brand-name">VELMORA</div>
    </div>

    <ul class="contact">
      <li>
        <svg viewBox="0 0 24 24" aria-hidden="true"><path d="M6.6 10.8a15 15 0 0 0 6.6 6.6l2.2-2.2a1 1 0 0 1 1-.25 11.4 11.4 0 0 0 3.6.6 1 1 0 0 1 1 1V20a1 1 0 0 1-1 1A17 17 0 0 1 3 4a1 1 0 0 1 1-1h3.5a1 1 0 0 1 1 1c0 1.25.2 2.45.6 3.6a1 1 0 0 1-.25 1z"/></svg>
        958-214-3380
      </li>
      <li>
        <svg viewBox="0 0 24 24" aria-hidden="true"><path d="M12 2a10 10 0 1 0 0 20 10 10 0 0 0 0-20zm6.9 6h-2.9a15.6 15.6 0 0 0-1.4-3.6A8 8 0 0 1 18.9 8zM12 4c.8 1.2 1.5 2.5 1.9 4h-3.8c.4-1.5 1.100-2.8 1.9-4zM4.3 14a8.2 8.2 0 0 1 0-4h3.4a16 16 0 0 0 0 4zm.8 2h2.9c.3 1.3.8 2.5 1.4 3.6A8 8 0 0 1 5.1 16zM8 8H5.1a8 8 0 0 1 4.3-3.6C8.8 5.5 8.3 6.7 8 8zm4 12c-.8-1.2-1.5-2.5-1.9-4h3.8c-.4 1.5-1.1 2.8-1.9 4zm2.3-6H9.7a14.6 14.6 0 0 1 0-4h4.6a14.6 14.6 0 0 1 0 4zm.3 5.6c.6-1.1 1.1-2.3 1.4-3.6h2.9a8 8 0 0 1-4.3 3.6zM16.3 14a16 16 0 0 0 0-4h3.4a8.2 8.2 0 0 1 0 4z"/></svg>
        www.velmora.com.mx
      </li>
      <li>
        <svg viewBox="0 0 24 24" aria-hidden="true"><path d="M12 2a7 7 0 0 0-7 7c0 5.2 7 13 7 13s7-7.8 7-13a7 7 0 0 0-7-7zm0 9.5A2.5 2.5 0 1 1 12 6.5a2.5 2.5 0 0 1 0 5z"/></svg>
        Jacaranda 415, Bahía Serena, Costa Azul CP 48210
      </li>
    </ul>

    <div class="rule"></div>
    <div class="band"></div>
    <div class="agave-art" role="img" aria-label="Dark burgundy silhouette illustration of an agave plant resting on the bottom band"></div>
  </main>
</body>
</html>
```